Construction company business card

One side to be the logo with the company name, The other side I would like: (Tomas verbick) Project manager 41 barrow crescent hallam 52917306224783(03) 9703 2428Info@gudeljgroup.comAnd then maybe a couple dot points saying what we do:Construction (commercial & industrial) Civil construction

Anything else please contact me!
Maybe curved st one edge of the card

Target Market(s)

Older clientele

Industry/Entity Type

Construction Company

Contact Information for Business Card

Read above

Colors
3277b5
1b1b1b
9d9d9d

Requirements
Must have
• Use my logo on one side
Nice to have
• Read above
Should not have
• Read above

```html
<!DOCTYPE html>
<html lang="en">
<head>
<meta charset="utf-8">
<title>Strongline Property Group – Business Card</title>
<link href="https://fonts.googleapis.com/css2?family=Roboto:wght@400;700&display=swap" rel="stylesheet">
<style>
  :root {
    --backdrop: #2a2a2b;
    --card: #111214;
    --blue: #3277b5;
    --grey: #9d9d9d;
    --white: #f2f2f2;
  }
  * { margin: 0; padding: 0; box-sizing: border-box; }
  html, body {
    width: 1200px; height: 1138px; overflow: hidden;
    background: var(--backdrop);
    font-family: "Roboto", Arial, sans-serif;
  }
  .card {
    position: absolute;
    width: 620px; height: 376px;
    background: var(--card);
    border-radius: 0 30px 0 30px;
    overflow: hidden;
    box-shadow: 0 4px 12px rgba(0,0,0,.5);
  }
  .card--front { left: 274px; top: 185px; }
  .card--back  { left: 276px; top: 607px; }

  .brand-name {
    color: var(--blue);
    font-weight: 700;
    text-transform: uppercase;
    line-height: 1;
  }

  /* front */
  .front-dot {
    position: absolute; left: 247px; top: 45px;
    width: 124px; height: 124px; border-radius: 50%;
    background: var(--blue);
  }
  .front-brand {
    position: absolute; left: 0; right: 0; top: 212px;
    text-align: center;
  }
  .front-brand .line1 { font-size: 44px; letter-spacing: 1px; }
  .front-brand .line2 { font-size: 17px; letter-spacing: 7px; margin-top: 6px; }
  .website {
    position: absolute; left: 0; right: 0; top: 302px;
    display: flex; justify-content: center; align-items: center; gap: 10px;
    color: var(--white); font-size: 16px;
  }
  .website::before, .website::after {
    content: ""; width: 42px; height: 2px; background: var(--blue);
  }
  .services-line {
    position: absolute; left: 0; right: 0; top: 330px;
    text-align: center; color: var(--white); font-size: 16.5px;
  }
  .stripe {
    position: absolute; left: 0; right: 0; bottom: 0; height: 17px;
    display: flex;
  }
  .stripe .grey { flex: 0 0 50%; background: var(--grey); }
  .stripe .blue { flex: 1; background: var(--blue); }

  /* back */
  .back-disc {
    position: absolute; left: -36px; top: 21px;
    width: 338px; height: 338px; border-radius: 50%;
    background: var(--blue);
  }
  .back-info { position: absolute; left: 317px; top: 42px; color: var(--white); }
  .back-info .line1 { font-size: 38px; letter-spacing: 1px; }
  .back-info .line2 { font-size: 15px; letter-spacing: 7px; margin-top: 4px; }
  .person-name { margin-top: 26px; color: var(--blue); font-weight: 700; font-size: 23px; }
  .person-role { margin-top: 2px; font-size: 16.5px; }
  .contact-list { list-style: none; margin-top: 16px; font-size: 16.5px; }
  .contact-list li { display: flex; align-items: center; height: 24px; }
  .contact-list svg { width: 14px; height: 14px; margin-right: 18px; fill: var(--blue); }
  .address { margin-top: 2px; font-size: 16.5px; }
  .services { margin-top: 8px; color: var(--blue); font-size: 15.5px; line-height: 22px; }
</style>
</head>
<body>

<section class="card card--front">
  <div class="front-dot"></div>
  <div class="front-brand brand-name">
    <div class="line1">Strongline</div>
    <div class="line2">Property Group</div>
  </div>
  <div class="website">www.stronglineproperty.com</div>
  <p class="services-line">Construction (Commercial &amp; Industrial) Civil Construction</p>
  <div class="stripe"><span class="grey"></span><span class="blue"></span></div>
</section>

<section class="card card--back">
  <div class="back-disc"></div>
  <div class="back-info">
    <div class="brand-name">
      <div class="line1">Strongline</div>
      <div class="line2">Property Group</div>
    </div>
    <p class="person-name">Tomas Verbick</p>
    <p class="person-role">Project Manager</p>
    <ul class="contact-list">
      <li><svg viewBox="0 0 16 16"><path d="M2 5c0-2 3-3 6-3s6 1 6 3v1h-3V5H5v1H2zM4 7h8l2 7H2z"/></svg>(73) 0622 4783</li>
      <li><svg viewBox="0 0 16 16"><path d="M1 3h14v10H1zM2.5 4.5 8 9l5.5-4.5v-.2H2.5z" fill-rule="evenodd"/></svg>(03) 9418 6573</li>
      <li><svg viewBox="0 0 16 16"><path d="M8 1a7 7 0 1 0 0 14A7 7 0 0 0 8 1zm-1 2v3H3.3A5 5 0 0 1 7 3zm2 0a5 5 0 0 1 3.7 3H9zM3.3 10H7v3a5 5 0 0 1-3.7-3zM9 10h3.7A5 5 0 0 1 9 13zM3 8h10" /></svg>info@verbickgroup.com</li>
    </ul>
    <p class="address">41 Barrow Crescent Ashvale 5291</p>
    <p class="services">Construction (Commercial<br>&amp; Industrial) Civil Construction</p>
  </div>
</section>

</body>
</html>
```